Construction business card

I need a new business card, they can connect with my logo, brand.
What we do is residential house , design and build
I like: Navy blue / black
I attached our logo, brand,
and, some idea for business card.

```html
<!DOCTYPE html>
<html lang="en">
<head>
<meta charset="utf-8">
<title>Harlow Ridge Builders – Business Card</title>
<link rel="stylesheet" href="https://fonts.googleapis.com/css2?family=Arimo:wght@400;700&display=swap">
<style>
  :root {
    --stage: #1d1e20;
    --card-blue: #3d88c9;
    --ink-white: #ffffff;
    --rule: rgba(255,255,255,0.75);
  }
  * { box-sizing: border-box; margin: 0; padding: 0; }
  html, body {
    width: 1200px; height: 801px; overflow: hidden;
    background: var(--stage);
    font-family: "Arimo", Arial, sans-serif;
    color: var(--ink-white);
  }
  .stage {
    width: 1200px; height: 801px;
    display: flex; align-items: center; justify-content: center; gap: 40px;
  }
  .card {
    position: relative;
    width: 540px; height: 309px;
    background: var(--card-blue);
    border-radius: 18px;
    overflow: hidden;
  }
  /* front */
  .card--front .brand {
    position: absolute; left: 0; top: 0; width: 252px; height: 100%;
    display: flex; align-items: center; justify-content: center; gap: 12px;
  }
  .card--front .divider {
    position: absolute; left: 252px; top: 62px; bottom: 62px;
    width: 1px; background: var(--rule);
  }
  .brand__mark {
    width: 16px; height: 16px; background: var(--ink-white); flex: none;
  }
  .brand__name {
    font-weight: 700; text-transform: uppercase; line-height: 1.05;
    letter-spacing: 0.5px;
  }
  .card--front .brand__name { font-size: 25px; }
  .details {
    position: absolute; left: 286px; top: 62px; right: 20px;
  }
  .details__name {
    font-size: 17px; font-weight: 700; letter-spacing: 0.6px;
  }
  .details__role { font-size: 12px; margin-top: 3px; }
  .details__address { font-size: 12px; line-height: 1.35; margin-top: 16px; }
  .contact { list-style: none; margin-top: 14px; font-size: 12px; }
  .contact li { display: flex; align-items: center; gap: 7px; line-height: 1.55; }
  .contact svg { width: 11px; height: 11px; flex: none; }
  /* back */
  .card--back .brand {
    position: absolute; inset: 0;
    display: flex; align-items: center; justify-content: center; gap: 16px;
  }
  .card--back .brand__mark { width: 22px; height: 22px; }
  .card--back .brand__name { font-size: 36px; }
</style>
</head>
<body>
<main class="stage">
  <section class="card card--front" aria-label="Business card front">
    <div class="brand">
      <span class="brand__mark"></span>
      <p class="brand__name">Harlow Ridge<br>Builders</p>
    </div>
    <div class="divider"></div>
    <div class="details">
      <h1 class="details__name">DANIEL MERCER</h1>
      <p class="details__role">CEO/Founder</p>
      <p class="details__address">42 Fernhill Ave,<br>Oakvale, VIC 3190</p>
      <ul class="contact">
        <li>
          <svg viewBox="0 0 12 12" aria-hidden="true"><path fill="#fff" d="M2.5 1l2 2.2-1 1.3c.7 1.5 1.8 2.6 3.2 3.2l1.3-1 2.1 2-1.2 1.8C5 10.3 1.7 7 .7 2.2z"/></svg>
          0400 555 018
        </li>
        <li>
          <svg viewBox="0 0 12 12" aria-hidden="true"><path fill="#fff" d="M1 3h10v6.5H1z"/><path fill="none" stroke="#3d88c9" stroke-width="1" d="M1.3 3.3L6 7l4.7-3.7"/></svg>
          hello@harlowridgebuilders.com.au
        </li>
        <li>
          <svg viewBox="0 0 12 12" aria-hidden="true"><circle cx="6" cy="6" r="5" fill="#fff"/><path fill="none" stroke="#3d88c9" stroke-width=".8" d="M1 6h10M6 1c-2 2.8-2 7.2 0 10M6 1c2 2.8 2 7.2 0 10"/></svg>
          harlowridgebuilders.com.au
        </li>
      </ul>
    </div>
  </section>
  <section class="card card--back" aria-label="Business card back">
    <div class="brand">
      <span class="brand__mark"></span>
      <p class="brand__name">Harlow Ridge<br>Builders</p>
    </div>
  </section>
</main>
</body>
</html>
```